Valderons Business Card

Business card for philanthropic organization

Industry/Entity Type

Business

Contact Information for Business Card

Need a very ELEGANT, sober, embossed, formal business card... it should transmit CREDIBILITY. Not looking for a "fun card". would like white, grays or black designs.

Font styles to use
Script

Requirements
Must have
• Embossed look

```html
<!DOCTYPE html>
<html lang="en">
<head>
<meta charset="utf-8">
<title>Valderons Business Card</title>
<link rel="stylesheet" href="https://fonts.googleapis.com/css2?family=Lobster&family=Roboto:wght@400;500&display=swap">
<style>
  :root {
    --backdrop: #d9d6d2;
    --card: #1c1c1d;
    --card-edge: #101011;
    --emboss-dark: #0b0b0c;
    --emboss-light: #3a3a3c;
    --ink: #f2f2f2;
    --ink-soft: #d8d8d8;
    --metal: #b9b9bd;
  }
  * { box-sizing: border-box; margin: 0; padding: 0; }
  html, body { width: 1200px; height: 934px; overflow: hidden; }
  body {
    background: var(--backdrop);
    display: flex;
    align-items: center;
    justify-content: center;
    font-family: "Roboto", Arial, sans-serif;
  }
  .card {
    position: relative;
    width: 1000px;
    height: 572px;
    background: radial-gradient(ellipse at 30% 20%, #262627 0%, var(--card) 55%, var(--card-edge) 100%);
    border-radius: 6px;
    box-shadow: 0 18px 40px rgba(0,0,0,0.35);
    color: var(--ink);
  }
  .card__name {
    position: absolute;
    left: 72px;
    top: 52px;
    font-family: "Lobster", cursive;
    font-size: 58px;
    color: #19191a;
    text-shadow: -1px -1px 0 var(--emboss-light), 2px 2px 2px var(--emboss-dark);
  }
  .card__title {
    position: absolute;
    left: 78px;
    top: 136px;
    font-size: 22px;
    line-height: 1.3;
    color: var(--ink-soft);
  }
  .card__contacts {
    position: absolute;
    left: 78px;
    top: 330px;
    list-style: none;
    font-size: 22px;
    line-height: 1.35;
  }
  .card__contacts li {
    display: flex;
    align-items: center;
    gap: 14px;
  }
  .card__contacts .icon {
    width: 18px;
    height: 18px;
    flex: none;
    fill: var(--ink);
  }
  .card__contacts .no-icon { width: 18px; flex: none; }
  .card__mark {
    position: absolute;
    right: 90px;
    bottom: 80px;
    display: flex;
    align-items: center;
    gap: 14px;
    font-size: 34px;
    font-weight: 500;
    color: var(--metal);
  }
  .card__mark-dot {
    width: 22px;
    height: 22px;
    border-radius: 50%;
    background: var(--metal);
  }
</style>
</head>
<body>
  <section class="card">
    <h1 class="card__name">Lisandro Quintero</h1>
    <p class="card__title">Dar Salem Valderons<br>Potentate 2017</p>
    <ul class="card__contacts">
      <li>
        <svg class="icon" viewBox="0 0 18 18" aria-hidden="true"><rect x="4" y="1" width="10" height="16" rx="2"/><rect x="6" y="3" width="6" height="10" fill="#1c1c1d"/></svg>
        +(000)-5550-1234
      </li>
      <li>
        <svg class="icon" viewBox="0 0 18 18" aria-hidden="true"><rect x="1" y="4" width="16" height="11" rx="1"/><path d="M2 5 L9 11 L16 5" stroke="#1c1c1d" stroke-width="1.6" fill="none"/></svg>
        lquintero@mailbox.com
      </li>
      <li>
        <svg class="icon" viewBox="0 0 18 18" aria-hidden="true"><path d="M9 1a6 6 0 0 0-6 6c0 4.5 6 10 6 10s6-5.5 6-10a6 6 0 0 0-6-6z"/><circle cx="9" cy="7" r="2.2" fill="#1c1c1d"/></svg>
        P.O. Box 0000-12345
      </li>
      <li><span class="no-icon"></span>Vistamar, Republic of Oriana</li>
    </ul>
    <div class="card__mark">
      <span class="card__mark-dot"></span>
      <span>Valderons</span>
    </div>
  </section>
</body>
</html>
```